RW Holloway LLC Business Card - Civil Engineering & Consulting Firm

We need a Business Card that is elegant, and masculine.  It is our Professional Civil Engineering & Consulting Company located in San Antonio TX (Not s construction or builder firm- no gears & no tool images please). We provide civil engineering services including  commercial site plans, grading and drainage plans, utility plans, hydraulics and hydrology, land planning, utility coordination, and other general civil engineering services related to commercial and residential development.
We have 2 existing Logos. We would like to convey reliability, strength, trustworthiness and attention to detail.  Blues and orange tones as per logo We are OK with the use of a darker blue in the mix.  We have 2 logo versions - Full Company Name Logo to go on the back of card, & Small Icon Logo for the front w/ personal Info.

Target Market(s)
Architects, Real Estate Developers, Other Strctural Engineers, Surveyers, General Contractors
Industry/Entity Type
Professional Civil Engineering
Contact Information for Business Card
Name, Position, Address, Cell & Office #, email, and company website
Font styles to use
Other font styles liked:
- Avian
Requirements
Should not have
- No Tools, No Gears, no Cranes, or Construction Equipment.

```html
<!DOCTYPE html>
<html lang="en">
<head>
<meta charset="utf-8">
<title>RW Holloway LLC — Business Card</title>
<link href="https://fonts.googleapis.com/css2?family=Montserrat:wght@400;500;700;800&display=swap" rel="stylesheet">
<style>
  :root {
    --backdrop: #1d1d1f;
    --card: #ffffff;
    --card-shade: #efeeee;
    --orange: #f0922b;
    --blue: #7aaedb;
    --ink: #1a1a1a;
  }
  * { box-sizing: border-box; margin: 0; padding: 0; }
  html, body { width: 1200px; height: 900px; overflow: hidden; }
  body {
    background: var(--backdrop);
    font-family: "Montserrat", Arial, sans-serif;
    display: flex;
    align-items: center;
    justify-content: center;
    gap: 50px;
  }
  .card {
    position: relative;
    width: 540px;
    height: 309px;
    border-radius: 22px;
    background: linear-gradient(135deg, var(--card) 55%, var(--card-shade));
    box-shadow: 0 5px 0 var(--orange), 0 18px 30px rgba(0,0,0,.45);
    overflow: hidden;
  }
  /* Front: personal details */
  .card-front .name-block {
    position: absolute;
    top: 34px;
    left: 0;
    padding-left: 46px;
  }
  .card-front .name-marker {
    position: absolute;
    left: 0;
    top: 2px;
    width: 26px;
    height: 24px;
    background: var(--orange);
  }
  .person-name {
    color: var(--orange);
    font-weight: 800;
    font-size: 22px;
    letter-spacing: .5px;
    text-transform: uppercase;
  }
  .person-title {
    color: var(--ink);
    font-size: 15px;
    margin-top: 2px;
  }
  .contact-list {
    position: absolute;
    left: 30px;
    bottom: 36px;
    list-style: none;
  }
  .contact-list li {
    display: flex;
    align-items: center;
    gap: 12px;
    font-size: 15px;
    font-weight: 500;
    color: var(--ink);
    line-height: 25px;
  }
  .contact-list svg { width: 15px; height: 15px; fill: var(--orange); flex: none; }
  .brand-mark {
    position: absolute;
    right: 44px;
    top: 120px;
    display: flex;
    align-items: center;
    gap: 8px;
    color: var(--blue);
    font-weight: 500;
    font-size: 17px;
    letter-spacing: 1px;
  }
  .brand-mark .brand-square {
    width: 14px; height: 14px; background: var(--orange);
  }
  .address {
    position: absolute;
    right: 34px;
    bottom: 30px;
    text-align: left;
    font-size: 15px;
    font-weight: 500;
    color: var(--ink);
    line-height: 22px;
  }
  /* Back: company name */
  .card-back {
    display: flex;
    align-items: center;
    justify-content: center;
  }
  .company-name {
    color: var(--blue);
    font-weight: 500;
    font-size: 40px;
    letter-spacing: 2px;
    text-transform: uppercase;
    text-align: center;
    line-height: 1.15;
  }
</style>
</head>
<body>
  <section class="card card-front" aria-label="Card front">
    <div class="name-block">
      <span class="name-marker"></span>
      <h1 class="person-name">Dale Harmon</h1>
      <p class="person-title">Co-Founder</p>
    </div>

    <div class="brand-mark"><span class="brand-square"></span>RW Holloway LLC</div>

    <ul class="contact-list">
      <li><svg viewBox="0 0 24 24"><path d="M6.6 10.8a15 15 0 0 0 6.6 6.6l2.2-2.2a1 1 0 0 1 1-.25 11.4 11.4 0 0 0 3.6.57 1 1 0 0 1 1 1V20a1 1 0 0 1-1 1A17 17 0 0 1 3 4a1 1 0 0 1 1-1h3.5a1 1 0 0 1 1 1c0 1.25.2 2.45.57 3.57a1 1 0 0 1-.25 1z"/></svg>210-555-0142</li>
      <li><svg viewBox="0 0 24 24"><path d="M3 8c0-2 4-4 9-4s9 2 9 4v2h-5V8H8v2H3z"/><rect x="5" y="11" width="14" height="9" rx="2"/></svg>210-555-0187</li>
      <li><svg viewBox="0 0 24 24"><path d="M2 5h20v14H2z M2 5l10 8 10-8" stroke="#fff" stroke-width="1.2"/></svg>info@rwhollowayllc</li>
      <li><svg viewBox="0 0 24 24"><circle cx="12" cy="12" r="10"/></svg>www.rwholloway.com</li>
    </ul>

    <address class="address">4410 S. Presa Street<br>Suite 210 San Antonio</address>
  </section>

  <section class="card card-back" aria-label="Card back">
    <p class="company-name">RW Holloway LLC</p>
  </section>
</body>
</html>
```